Hartwell Estates Business Cards

I would like a business card that includes myself and my partner.
Includes: Logo, office #, email, website, our names, our numbers and possibly the address. I would also like the logo to be embossed and the card to be horizontal.
There is a photo of our yard signs to give you an idea of the colors of our business.

Target Market(s)

Everyone in real estate market.
We are in a rural area. Our clientele are from all socioeconomic backgrounds.

Industry/Entity Type

Real Estate Agent

Contact Information for Business Card

Company Name: Hartwell Estates
Our Names, Titles & Cell #'s : Dana Pembrook-Broker (555).317.6624, Marla Pembrook-Realtor (555).609.1385
Office #: (555).240.3918
Website: hartwellestates-demo.com
Joint Email: pembrook@hartwellestates-demo.com
Office Address: 418B W. Calloway Ave.
Fenwick, OR. 70913

Font styles to use
Serif

Requirements
Must have
• HORIZONTAL, Logo, Myself and my partners names, Our cell #'s, our office #, our website, our email address
Nice to have
• Embossed logo, office address, our titles.

```html
<!DOCTYPE html>
<html lang="en">
<head>
<meta charset="utf-8">
<title>Hartwell Estates – Business Card</title>
<link rel="stylesheet" href="https://fonts.googleapis.com/css2?family=Crimson+Pro:wght@600&family=Libre+Baskerville:wght@700&display=swap">
<style>
  :root {
    --brand-purple: #4a2263;
    --card-white: #ffffff;
  }
  html, body {
    margin: 0;
    padding: 0;
    overflow: hidden;
    background: var(--card-white);
  }
  .card {
    position: relative;
    width: 1200px;
    height: 720px;
    overflow: hidden;
    background: var(--card-white);
    font-family: "Libre Baskerville", Georgia, serif;
    font-weight: 700;
  }
  .skyline {
    position: absolute;
    left: 0;
    top: 256px;
    width: 1200px;
    height: 464px;
    background: var(--brand-purple);
  }
  .brand {
    position: absolute;
    left: 704px;
    top: 58px;
    width: 414px;
    text-align: center;
    color: var(--brand-purple);
    font-family: "Crimson Pro", Georgia, serif;
    font-weight: 600;
    line-height: 1;
  }
  .brand-name { font-size: 92px; letter-spacing: 1px; }
  .brand-rule {
    height: 3px;
    margin: 8px 4px 0;
    background: var(--brand-purple);
  }
  .brand-sub { font-size: 54px; margin-top: 10px; }
  .agents {
    position: absolute;
    left: 81px;
    top: 386px;
    color: var(--card-white);
  }
  .agent { margin-bottom: 60px; }
  .agent-name {
    font-size: 30px;
    letter-spacing: 1.5px;
    line-height: 36px;
  }
  .agent-title {
    font-size: 22px;
    letter-spacing: 1px;
    line-height: 30px;
  }
  .agent-phone {
    font-size: 24px;
    letter-spacing: 1.5px;
    line-height: 34px;
  }
  .contact-list {
    position: absolute;
    left: 661px;
    top: 392px;
    margin: 0;
    padding: 0;
    list-style: none;
    color: var(--card-white);
  }
  .contact-item {
    display: flex;
    align-items: flex-start;
    margin-bottom: 25px;
    font-size: 19px;
    letter-spacing: 1.2px;
    line-height: 36px;
  }
  .contact-icon {
    width: 36px;
    height: 36px;
    flex: none;
    margin-right: 24px;
  }
</style>
</head>
<body>
<main class="card">
  <div class="skyline" role="img" aria-label="City skyline silhouette in brand purple"></div>

  <div class="brand">
    <div class="brand-name">HARTWELL</div>
    <div class="brand-rule"></div>
    <div class="brand-sub">Estates</div>
  </div>

  <section class="agents">
    <div class="agent">
      <div class="agent-name">DANA PEMBROOK</div>
      <div class="agent-title">Broker</div>
      <div class="agent-phone">(555).317.6624</div>
    </div>
    <div class="agent">
      <div class="agent-name">MARLA PEMBROOK</div>
      <div class="agent-title">Realtor</div>
      <div class="agent-phone">(555).609.1385</div>
    </div>
  </section>

  <ul class="contact-list">
    <li class="contact-item">
      <svg class="contact-icon" viewBox="0 0 36 36" aria-hidden="true">
        <circle cx="18" cy="18" r="18" fill="#fff"/>
        <rect x="11" y="9" width="14" height="18" rx="2" fill="none" stroke="#4a2263" stroke-width="2.4"/>
        <path d="M15 13c0 5 3 9 7 10l1.5-2-2.5-1.5-1 1c-1.5-.8-2.7-2.3-3-4l1-.8-1.2-2.7z" fill="#4a2263"/>
      </svg>
      <span>(555).240.3918</span>
    </li>
    <li class="contact-item">
      <svg class="contact-icon" viewBox="0 0 36 36" aria-hidden="true">
        <circle cx="18" cy="18" r="18" fill="#fff"/>
        <g fill="none" stroke="#4a2263" stroke-width="1.8">
          <circle cx="18" cy="18" r="9"/>
          <ellipse cx="18" cy="18" rx="4" ry="9"/>
          <line x1="9" y1="18" x2="27" y2="18"/>
          <line x1="10.5" y1="13.5" x2="25.5" y2="13.5"/>
          <line x1="10.5" y1="22.5" x2="25.5" y2="22.5"/>
        </g>
      </svg>
      <span>hartwellestates-demo.com</span>
    </li>
    <li class="contact-item">
      <svg class="contact-icon" viewBox="0 0 36 36" aria-hidden="true">
        <circle cx="18" cy="18" r="18" fill="#fff"/>
        <rect x="9" y="12" width="18" height="13" rx="1.5" fill="#4a2263"/>
        <path d="M9.5 12.5 18 19l8.5-6.5" fill="none" stroke="#fff" stroke-width="1.6"/>
      </svg>
      <span>pembrook@hartwellestates-demo.com</span>
    </li>
    <li class="contact-item">
      <svg class="contact-icon" viewBox="0 0 36 36" aria-hidden="true">
        <circle cx="18" cy="18" r="18" fill="#fff"/>
        <path d="M18 8a6.5 6.5 0 0 0-6.5 6.5C11.5 19.5 18 26 18 26s6.5-6.5 6.5-11.5A6.5 6.5 0 0 0 18 8z" fill="#4a2263"/>
        <circle cx="18" cy="14.5" r="2.4" fill="#fff"/>
        <ellipse cx="18" cy="27" rx="7" ry="1.8" fill="none" stroke="#4a2263" stroke-width="1.4"/>
      </svg>
      <span>418B W. Calloway Ave.<br>Fenwick, OR. 70913</span>
    </li>
  </ul>
</main>
</body>
</html>
```